sydney wedding photography business needs a business card design

we need a business card design for a sydney based wedding photography and videography business. our business name is :golden hour studio and film. our target clients are 24-35 yrs female. our style is candid, organic, natural, dynamic. we are a team of young photographers and videographers, and help brides to create memories that they will cherish for the rest of their lives. the logo will be provided. we want an elegant design that reflects our style, and also want to give a great impression to our clients that we are one of the best studios in sydney and our brand means quality and premium service.

Target Market(s)

bride to be, 24-35 years old, living in sydney and surrunding areas

Industry/Entity Type

Wedding Photography

Contact Information for Business Card

address: 57 tarrant street, glenmore nsw 2047
mobile: 0431872259
phone: (02) 9163 2408
info@tidewillowstudio.net.au
www.tidewillowstudio.net.au
facebook:tidewillowweddings
instagram:tidewillowweddings

Font styles to use
Serif
Sans Serif

Requirements
Nice to have
• maybe add my slogan"memories beyond eternity" if the layout looks good
Should not have
• no black color, not good idea for wedding biz card

```html
<!DOCTYPE html>
<html lang="en">
<head>
<meta charset="utf-8">
<title>Golden Hour Studio and Film – Business Card</title>
<link rel="stylesheet" href="https://fonts.googleapis.com/css2?family=Dancing+Script:wght@600&family=Open+Sans:wght@400;600&display=swap">
<style>
  :root {
    --backdrop: #ecebe8;
    --gold-deep: #e3a90c;
    --gold-bright: #f4c312;
    --gold-ink: #d49d10;
    --card-white: #ffffff;
    --ink-soft: #3f3a36;
    --emboss-light: #f3f2f0;
    --emboss-shade: #e6e4e0;
    --card-shadow: rgba(60, 45, 20, 0.18);
  }
  * { box-sizing: border-box; margin: 0; padding: 0; }
  html, body {
    width: 1200px; height: 900px; overflow: hidden;
    background: var(--backdrop);
  }
  .canvas { position: relative; width: 1200px; height: 900px; }

  .card {
    position: absolute;
    width: 600px; height: 343px;
    border-radius: 4px;
    box-shadow: 0 10px 28px var(--card-shadow);
    overflow: hidden;
  }

  /* Front face */
  .card--front {
    left: 90px; top: 110px;
    background: linear-gradient(170deg, var(--gold-deep) 0%, var(--gold-bright) 100%);
  }
  .card--front .emboss-mark {
    position: absolute; right: 30px; top: 28px;
    width: 120px; height: 110px;
    border-radius: 6px;
    background: linear-gradient(135deg, rgba(255,255,255,0.12), rgba(255,255,255,0));
  }
  .card--front .brand-name {
    position: absolute; left: 0; right: 0; top: 104px;
    text-align: center;
    font: 600 34px/1.15 "Open Sans", sans-serif;
    letter-spacing: 1px;
    color: var(--card-white);
  }
  .social-row {
    position: absolute; left: 0; right: 0; top: 222px;
    display: flex; justify-content: center; gap: 10px;
  }
  .social-row span {
    width: 26px; height: 26px; border-radius: 4px;
    background: var(--card-white);
  }

  /* Back face */
  .card--back {
    left: 510px; top: 450px;
    background: var(--card-white);
  }
  .card--back .emboss-mark {
    position: absolute; left: 36px; top: 40px;
    width: 190px; height: 190px;
    border-radius: 8px;
    background: linear-gradient(135deg, var(--emboss-light), var(--emboss-shade));
  }
  .contact {
    position: absolute; left: 300px; top: 36px;
    color: var(--ink-soft);
    font: 400 12.5px/1.45 "Open Sans", sans-serif;
  }
  .contact .person-name {
    font: 600 26px/1 "Dancing Script", cursive;
    color: var(--gold-ink);
  }
  .contact .person-role { margin-bottom: 12px; }
  .contact .line { display: flex; align-items: center; gap: 8px; }
  .contact .line svg { width: 11px; height: 11px; fill: var(--gold-ink); }
  .contact .address { margin-top: 12px; padding-left: 19px; }
  .card--back .brand-name {
    position: absolute; right: 34px; bottom: 36px;
    text-align: right;
    font: 600 30px/1.15 "Open Sans", sans-serif;
    letter-spacing: 1px;
    color: var(--gold-ink);
  }
</style>
</head>
<body>
<main class="canvas">
  <section class="card card--front">
    <div class="emboss-mark" role="img" aria-label="Faint embossed gem decoration"></div>
    <h1 class="brand-name">Golden Hour<br>Studio and Film</h1>
    <div class="social-row" aria-label="Social media">
      <span></span><span></span><span></span><span></span>
    </div>
  </section>

  <section class="card card--back">
    <div class="emboss-mark" role="img" aria-label="Faint embossed gem decoration"></div>
    <div class="contact">
      <p class="person-name">Marcus Ellery</p>
      <p class="person-role">Managing Director</p>
      <p class="line">
        <svg viewBox="0 0 24 24" aria-hidden="true"><path d="M6.6 10.8a15.1 15.1 0 0 0 6.6 6.6l2.2-2.2c.3-.3.7-.4 1-.2 1.1.4 2.3.6 3.6.6.6 0 1 .4 1 1V20c0 .6-.4 1-1 1A17 17 0 0 1 3 4c0-.6.4-1 1-1h3.5c.6 0 1 .4 1 1 0 1.3.2 2.5.6 3.6.1.3 0 .7-.2 1z"/></svg>
        (02) 9163 2408
      </p>
      <p class="line">
        <svg viewBox="0 0 24 24" aria-hidden="true"><path d="M2 5h20v14H2z M3 6l9 7 9-7"/></svg>
        info@tidewillowstudio.net.au
      </p>
      <p class="address">57 Tarrant Street,<br>Glenmore NSW 2047</p>
    </div>
    <p class="brand-name">Golden Hour<br>Studio and Film</p>
  </section>
</main>
</body>
</html>
```